Redesign of LumoWordfind.com in Bootstrap 4

Current design of LumoWordfind.com is not responsive. We need to change it to latest version of Bootstrap 4 keeping essential elements in place.

Apart from home page, we need designs for http://www.lumowordfind.com/meaning/cat also.

Coding

Number of Pages Required

2 page

Colors
34a7d8

Requirements
Must have
• Bootstrap 4

```html
<!DOCTYPE html>
<html lang="en">
<head>
<meta charset="utf-8">
<title>LumoWordfind.com</title>
<link href="https://fonts.googleapis.com/css2?family=Raleway:wght@300;400;500;600&family=Noto+Serif:wght@400&display=swap" rel="stylesheet">
<style>
:root{
  --brand:#34a7d8;
  --brand-dark:#1f7fc0;
  --nav-top:#4fb8e6;
  --nav-bottom:#2f9bd6;
  --orange:#f7941d;
  --ink:#333;
  --line:#d5d5d5;
  --footer:#ededed;
  --bottom:#f4f4f4;
}
*{box-sizing:border-box;margin:0;padding:0}
html,body{width:748px;height:1200px;overflow:hidden;background:#fff}
body{position:relative;font-family:"Raleway",sans-serif;color:var(--ink)}
.abs{position:absolute}
/* header */
.logo{left:84px;top:20px;font:600 17px "Raleway",sans-serif;color:var(--brand-dark);display:flex;align-items:center;gap:6px}
.logo .dot{width:11px;height:11px;background:var(--orange);border-radius:50%}
.field{top:23px;height:18px;border:1px solid #ccc;background:#f2f2f2;font-size:7px;color:#888;padding:4px 6px}
.login-btn{left:638px;top:23px;width:43px;height:18px;background:var(--orange);color:#fff;font-size:8px;text-align:center;line-height:18px}
.join-note{left:433px;top:45px;font-size:6.5px;color:#555}
/* nav */
.nav{left:0;top:62px;width:748px;height:32px;background:linear-gradient(var(--nav-top),var(--nav-bottom))}
.nav a{position:absolute;top:0;height:32px;line-height:32px;color:#fff;font-size:10px;text-align:center;text-decoration:none;border-right:1px solid rgba(255,255,255,.25)}
.nav a.active{background:var(--brand-dark)}
/* hero */
.hero{left:0;top:94px;width:748px;height:277px;background:linear-gradient(#f6f6f6,#ebebeb)}
.skyline{left:0;top:285px;width:748px;height:86px;background:linear-gradient(rgba(210,210,210,0),rgba(200,200,200,.4))}
.hero-art{left:380px;top:128px;width:300px;height:196px;
  background:radial-gradient(ellipse 46% 50% at 34% 52%,#fffdf7 0%,#f3ede0 55%,rgba(243,237,224,0) 100%),
             radial-gradient(ellipse 40% 46% at 70% 56%,#3fa9d6 0%,#8fd0ea 55%,rgba(143,208,234,0) 100%)}
.hero-kicker{left:88px;top:176px;font:400 17px "Noto Serif",serif;color:#444;letter-spacing:.5px}
.hero-title{left:88px;top:196px;font:400 28px "Noto Serif",serif;color:#111}
.search-box{left:90px;top:240px;width:194px;height:23px;border:1px solid #ccc;background:#fff;font-size:8px;color:#777;padding:6px 8px}
.search-btn{left:284px;top:240px;width:63px;height:23px;background:var(--orange);color:#fff;font-size:10px;text-align:center;line-height:23px}
.dots{left:341px;top:349px;display:flex;gap:3px}
.dots span{width:8px;height:8px;border-radius:50%;background:#333}
.dots span.on{background:#fff;border:1.5px solid var(--brand-dark)}
/* features */
.features{left:88px;top:379px;width:570px;height:135px;border:1px solid var(--line);display:flex;background:linear-gradient(#fff,#f0f0f0)}
.feature{flex:1;text-align:center;border-right:1px solid var(--line);padding-top:11px}
.feature:last-child{border-right:0}
.feature h3{font:400 13px "Raleway",sans-serif;color:var(--brand);margin-top:6px}
.feature p{font-size:7px;line-height:12px;color:#555;margin-top:5px;padding:0 16px}
.icon{height:45px;display:flex;justify-content:center;align-items:center}
/* master words */
.mw-title{left:84px;top:558px;font:300 20px "Raleway",sans-serif;color:#222}
.mw-lead{left:86px;top:588px;width:270px;font-size:8px;line-height:13.5px;color:#444}
.mw-body{left:86px;top:623px;width:268px;font-size:6.5px;line-height:13.5px;color:#555}
.read-more{left:84px;top:670px;width:73px;height:21px;background:var(--orange);color:#fff;font-size:7.5px;line-height:21px;text-align:center}
.mw-art{left:420px;top:546px;width:202px;height:166px;
  background:radial-gradient(ellipse 52% 48% at 50% 40%,#ffffff 0%,#eceeef 50%,#6a6d70 82%,rgba(106,109,112,0) 100%)}
/* mobile band */
.band{left:0;top:738px;width:748px;height:224px;background:linear-gradient(120deg,#5cc0ea,#2f9fd8)}
.band-art{left:138px;top:748px;width:154px;height:214px;border-radius:16px 16px 0 0;
  background:linear-gradient(170deg,#ffffff 0%,#f0f0f0 48%,#e6c0a0 74%,#c99573 100%)}
.band-title{left:357px;top:781px;font:300 20px "Raleway",sans-serif;color:#fff}
.band-text{left:358px;width:270px;font-size:6.5px;line-height:13.5px;color:#e8f6fd}
/* browse */
.browse-label{left:91px;top:984px;font-size:11.5px;color:var(--brand)}
.letters{left:198px;top:985px;display:flex;border:1px solid #bbb}
.letters span{width:17px;height:14px;line-height:14px;text-align:center;font-size:10px;color:#444;border-right:1px solid #bbb}
.letters span:last-child{border-right:0}
/* footer */
.footer{left:0;top:1017px;width:748px;height:142px;background:var(--footer)}
.fcol{top:1047px}
.fcol h4{font:400 10px "Raleway",sans-serif;color:#333;margin-bottom:4px;letter-spacing:.3px}
.fcol a{display:block;font-size:7px;color:#444;text-decoration:none;line-height:14.5px}
.social{display:flex;gap:3px;margin-top:6px}
.social span{width:18px;height:18px;border:1.5px solid #222;border-radius:50%}
.bottom{left:0;top:1159px;width:748px;height:41px;background:var(--bottom)}
.copy{left:94px;top:1175px;font-size:6.5px;color:#777}
</style>
</head>
<body>

<header>
  <div class="abs logo"><span class="dot"></span>LumoWordfind</div>
  <div class="abs field" style="left:433px;width:99px">Username</div>
  <div class="abs field" style="left:535px;width:99px">Password</div>
  <div class="abs login-btn">Login</div>
  <div class="abs join-note">Join for Free Now!</div>
</header>

<nav class="abs nav">
  <a class="active" style="left:90px;width:64px">Home</a>
  <a style="left:154px;width:67px">Idioms</a>
  <a style="left:221px;width:102px">Common Errors</a>
  <a style="left:323px;width:84px">Crossword</a>
  <a style="left:407px;width:56px">Blog</a>
  <a style="left:463px;width:90px">Join for Free</a>
  <a style="left:553px;width:69px;border-right:0">Contact</a>
</nav>

<section>
  <div class="abs hero"></div>
  <div class="abs skyline" role="img" aria-label="Faint line drawing of a city skyline"></div>
  <div class="abs hero-art" role="img" aria-label="Illustration of an open book turning into a tablet with flying letters"></div>
  <div class="abs hero-kicker">MAURIS VEL LACUS VITAE</div>
  <h1 class="abs hero-title" style="font-weight:400">Lumo English Dictionary</h1>
  <div class="abs search-box">Enter a word or Phrase</div>
  <div class="abs search-btn">Search</div>
  <div class="abs dots"><span class="on"></span><span></span><span></span><span></span></div>
</section>

<section class="abs features">
  <div class="feature">
    <div class="icon">
      <svg width="42" height="42" viewBox="0 0 42 42">
        <rect x="11" y="1" width="19" height="19" rx="3" fill="#34a7d8"/>
        <rect x="1" y="22" width="19" height="19" rx="3" fill="#34a7d8"/>
        <rect x="22" y="22" width="19" height="19" rx="3" fill="#34a7d8"/>
        <text x="20.5" y="16" font-size="14" fill="#fff" text-anchor="middle" font-family="Raleway,sans-serif">A</text>
        <text x="10.5" y="37" font-size="14" fill="#fff" text-anchor="middle" font-family="Raleway,sans-serif">B</text>
        <text x="31.5" y="37" font-size="14" fill="#fff" text-anchor="middle" font-family="Raleway,sans-serif">C</text>
      </svg>
    </div>
    <h3>English Tidbit</h3>
    <p>Mauris vel lacus vitae felis vestibulum volutpat Etiam est nunc venenatis in tristique eu imperdiet ac nisl Cum</p>
  </div>
  <div class="feature">
    <div class="icon">
      <svg width="42" height="42" viewBox="0 0 42 42"><circle cx="21" cy="21" r="20" fill="#34a7d8"/></svg>
    </div>
    <h3>Quickfind Addon</h3>
    <p>Mauris vel lacus vitae felis vestibulum volutpat Etiam est nunc venenatis in tristique eu imperdiet ac nisl Cum</p>
  </div>
  <div class="feature">
    <div class="icon">
      <svg width="40" height="40" viewBox="0 0 40 40">
        <rect x="1" y="1" width="38" height="38" fill="none" stroke="#34a7d8" stroke-width="2"/>
        <g fill="#34a7d8">
          <rect x="6" y="6" width="6" height="6"/><rect x="20" y="6" width="6" height="6"/>
          <rect x="13" y="13" width="6" height="6"/><rect x="27" y="13" width="6" height="6"/>
          <rect x="6" y="20" width="6" height="6"/><rect x="20" y="20" width="6" height="6"/>
          <rect x="13" y="27" width="6" height="6"/><rect x="27" y="27" width="6" height="6"/>
        </g>
      </svg>
    </div>
    <h3>Daily Crossword</h3>
    <p>Mauris vel lacus vitae felis vestibulum volutpat Etiam est nunc venenatis in tristique eu imperdiet ac nisl Cum</p>
  </div>
</section>

<section>
  <h2 class="abs mw-title">Search, Save and Master Words</h2>
  <p class="abs mw-lead">Curabitur iaculis tempus eros Curabitur vel mi sit amet magna malesuada ultrices Ut nisi erat fermentum vel congue id euismod</p>
  <p class="abs mw-body">commodo a mi Morbi ornare gravida elit Integer congue augue et malesuada iaculis ipsum dui aliquet felis at cursus magna nisl nec elit Praesent elementum elit at tellus nec ultricies sit amet porttitor mattis enim In massa libero interdum</p>
  <div class="abs read-more">READ MORE &#8250;</div>
  <div class="abs mw-art" role="img" aria-label="Illustration of an open book on a desktop monitor screen"></div>
</section>

<section>
  <div class="abs band"></div>
  <div class="abs band-art" role="img" aria-label="Photo of a hand holding a phone showing magnified dictionary text"></div>
  <h2 class="abs band-title">Designed for Pocketphone</h2>
  <p class="abs band-text" style="top:814px">Curabitur iaculis tempus eros Curabitur vel mi sit amet magna malesuada ultrices Ut nisi erat fermentum vel congue id euismod in elit Fusce ultricies orci</p>
  <p class="abs band-text" style="top:848px">commodo a mi Morbi ornare gravida elit Integer congue augue et malesuada iaculis ipsum dui aliquet felis at cursus magna nisl nec elit Praesent elementum elit at tellus nec ultricies sit amet porttitor mattis enim In massa libero interdum nec i</p>
</section>

<section>
  <div class="abs browse-label">Browse Dictionary</div>
  <div class="abs letters">
    <span>A</span><span>B</span><span>C</span><span>D</span><span>E</span><span>F</span><span>G</span><span>H</span><span>I</span><span>J</span><span>K</span><span>L</span><span>M</span><span>N</span><span>O</span><span>P</span><span>Q</span><span>R</span><span>S</span><span>T</span><span>U</span><span>V</span><span>W</span><span>X</span><span>Y</span><span>Z</span>
  </div>
</section>

<footer>
  <div class="abs footer"></div>
  <div class="abs fcol" style="left:103px"><h4>COMPANY</h4><a>Home</a><a>Idioms</a><a>Common Errors</a><a>Crossword</a></div>
  <div class="abs fcol" style="left:215px"><h4>RESOURCES</h4><a>Blog</a><a>Join for Free</a><a>Contact</a></div>
  <div class="abs fcol" style="left:322px"><h4>OTHERS</h4><a>Popular Words</a><a>Common Errors in English</a><a>Exam Prep Online</a></div>
  <div class="abs fcol" style="left:447px"><h4>SUPPORT</h4><a>Privacy Policy</a><a>Terms of Use</a><a>FAQ</a><a>Contact</a></div>
  <div class="abs fcol" style="left:564px"><h4>GET IN TOUCH</h4><a>Please connect with us on</a>
    <div class="social"><span></span><span></span><span></span><span></span></div>
  </div>
  <div class="abs bottom"></div>
  <div class="abs copy">© 2016 Company Name&nbsp; All right reserved&nbsp; Term of Use</div>
</footer>

</body>
</html>
```